RW Framewell Inc Business cards

We need business cards using our existing logo but slightly modified. Right now the logo says RW Loadbearing Masonry. We want to keep the RW part of the design, but replace the Structural Concrete portion with "FRAMEWELL". Please see the attached file.
Ideally this would be a blank template so we can add Different Names, titles, and phone numbers later.
On the one side we want only the logo and on the other side the detail. I'm attaching an example for you to see.
Please reach out with any other questions. Our address and other details will be given out once we find a design we like.

Target Market(s)

Construction Industry

```html
<!DOCTYPE html>
<html lang="en">
<head>
<meta charset="utf-8">
<title>RW Framewell Inc – Business Cards</title>
<link rel="stylesheet" href="https://fonts.googleapis.com/css2?family=Montserrat:wght@500;700&family=Roboto:wght@400;500&display=swap">
<style>
  :root {
    --backdrop: #5a7fb9;
    --brand-blue: #2d5f9e;
    --card-white: #f7f7f5;
    --ink-grey: #5c5c5c;
    --accent-grey: #6f6f6f;
  }
  html, body {
    margin: 0;
    padding: 0;
    width: 1200px;
    height: 852px;
    overflow: hidden;
    background: var(--backdrop);
  }
  .stage {
    position: relative;
    width: 1200px;
    height: 852px;
  }
  .card {
    position: absolute;
    top: 276px;
    width: 510px;
    height: 300px;
    border-radius: 22px;
    box-sizing: border-box;
  }
  .card--front {
    left: 60px;
    background: var(--brand-blue);
    display: flex;
    align-items: center;
    justify-content: center;
  }
  .card--back {
    left: 630px;
    background: var(--card-white);
  }
  .wordmark {
    display: flex;
    flex-direction: column;
    align-items: flex-start;
    font-family: "Montserrat", sans-serif;
    font-weight: 700;
    line-height: 1;
  }
  .wordmark__row {
    display: flex;
    align-items: center;
    gap: 12px;
  }
  .wordmark__square {
    width: 20px;
    height: 20px;
  }
  .wordmark__initials {
    font-size: 88px;
    letter-spacing: 2px;
  }
  .wordmark__name {
    font-size: 22px;
    letter-spacing: 6px;
    margin-top: 6px;
    margin-left: 32px;
  }
  .card--front .wordmark { color: #ffffff; }
  .card--front .wordmark__square { background: #ffffff; }
  .card--back .wordmark {
    position: absolute;
    left: 34px;
    top: 104px;
    color: var(--brand-blue);
  }
  .card--back .wordmark__square { background: var(--accent-grey); }
  .card--back .wordmark__initials { font-size: 64px; }
  .card--back .wordmark__name { font-size: 16px; letter-spacing: 4px; margin-left: 32px; }
  .details {
    position: absolute;
    left: 282px;
    top: 62px;
    font-family: "Roboto", sans-serif;
    color: var(--ink-grey);
  }
  .details__name {
    font-size: 19px;
    font-weight: 500;
    color: var(--brand-blue);
    margin: 0;
  }
  .details__title {
    font-size: 13px;
    margin: 2px 0 18px;
  }
  .details__list {
    list-style: none;
    margin: 0;
    padding: 0;
    font-size: 13px;
    line-height: 1.55;
  }
  .details__list li {
    display: flex;
    align-items: flex-start;
    gap: 9px;
  }
  .details__icon {
    width: 12px;
    height: 12px;
    flex: none;
    margin-top: 4px;
    fill: var(--ink-grey);
  }
</style>
</head>
<body>
<main class="stage">
  <section class="card card--front" aria-label="Card front">
    <div class="wordmark">
      <div class="wordmark__row">
        <span class="wordmark__square"></span>
        <span class="wordmark__initials">RW</span>
      </div>
      <span class="wordmark__name">FRAMEWELL</span>
    </div>
  </section>

  <section class="card card--back" aria-label="Card back">
    <div class="wordmark">
      <div class="wordmark__row">
        <span class="wordmark__square"></span>
        <span class="wordmark__initials">RW</span>
      </div>
      <span class="wordmark__name">FRAMEWELL</span>
    </div>

    <div class="details">
      <p class="details__name">Dana RW Ellis</p>
      <p class="details__title">Managing Director</p>
      <ul class="details__list">
        <li>
          <svg class="details__icon" viewBox="0 0 12 12" aria-hidden="true"><path d="M2.5 1h2l1 2.5-1.3 1a6 6 0 0 0 3.3 3.3l1-1.3L11 7.5v2a1.5 1.5 0 0 1-1.5 1.5A8.5 8.5 0 0 1 1 2.5 1.5 1.5 0 0 1 2.5 1z"/></svg>
          <span>555-010-2040</span>
        </li>
        <li>
          <svg class="details__icon" viewBox="0 0 12 12" aria-hidden="true"><path d="M1 2.5h10v7H1z M1 2.5l5 4 5-4" fill="none" stroke="#5c5c5c" stroke-width="1.2"/></svg>
          <span>dana@framewell.example</span>
        </li>
        <li>
          <svg class="details__icon" viewBox="0 0 12 12" aria-hidden="true"><circle cx="6" cy="6" r="5" fill="none" stroke="#5c5c5c" stroke-width="1.1"/><path d="M1 6h10M6 1c2 2.5 2 7.5 0 10M6 1c-2 2.5-2 7.5 0 10" fill="none" stroke="#5c5c5c" stroke-width="0.9"/></svg>
          <span>www.framewell.example</span>
        </li>
        <li>
          <svg class="details__icon" viewBox="0 0 12 12" aria-hidden="true"><path d="M6 0.8a3.6 3.6 0 0 0-3.6 3.6C2.4 7.2 6 11.2 6 11.2s3.6-4 3.6-6.8A3.6 3.6 0 0 0 6 0.8zm0 5a1.4 1.4 0 1 1 0-2.8 1.4 1.4 0 0 1 0 2.8z"/></svg>
          <span>410 Sample Ave., Any Town,<br>Westland, US 000000</span>
        </li>
      </ul>
    </div>
  </section>
</main>
</body>
</html>
```